Business Card for Vorla Parts Wholesale supplier

Hi There! I need a new business card for our company. We are specialized in selling Vorla parts, mostly we sell new LCD screens for Zelnar and Drelks. I would like to see that back in the design.

You can find the colors and logo's on our website: www.hartuvo.nl

Industry/Entity Type

Business

Contact Information for Business Card

My Details:
Tobias Lindqvist

Phone: 0031687203316
E-mail: Tobias@hartuvo.nl

Slogan: "Because Quality Matters"

Font styles to use
Sans Serif

Colors

Designer to choose colors to be used in the design.

Requirements
Must have
• A Black backside with the Hartuvo logo on it. The front side should be clean with only my contact details.
• But I'm also open for something really different or awesome!
Nice to have
• Remember that we are in the parts & repairing industry, So i'll be handing those business cards mainly to repair companies. Maybe you can do something with that thought :)

```html
<!DOCTYPE html>
<html lang="en">
<head>
<meta charset="utf-8">
<title>Hartuvo Business Card</title>
<link href="https://fonts.googleapis.com/css2?family=Open+Sans:wght@400;600;700&display=swap" rel="stylesheet">
<style>
  :root {
    --backdrop: #5a4a3c;
    --paper: #ffffff;
    --brand-orange: #f07225;
    --ink: #111111;
    --black: #000000;
    --white: #ffffff;
    --divider: #2a2a2a;
  }
  * { margin: 0; padding: 0; box-sizing: border-box; }
  html, body {
    width: 1200px;
    height: 987px;
    overflow: hidden;
    background: var(--backdrop);
    font-family: "Open Sans", sans-serif;
  }
  .canvas { position: relative; width: 1200px; height: 987px; }

  .card-front {
    position: absolute;
    left: 293px; top: 130px;
    width: 615px; height: 352px;
    display: flex;
    box-shadow: 0 2px 4px rgba(0,0,0,0.35);
  }
  .front-brand {
    width: 314px;
    background: var(--paper);
    display: flex;
    align-items: center;
    justify-content: center;
    gap: 12px;
  }
  .brand-dot {
    width: 34px; height: 34px;
    border-radius: 50%;
    background: var(--brand-orange);
  }
  .brand-name {
    font-size: 44px;
    font-weight: 700;
    color: var(--ink);
    letter-spacing: -0.5px;
  }
  .front-divider { width: 4px; background: var(--divider); border-left: 1px solid var(--paper); border-right: 1px solid var(--paper); }
  .front-contact {
    flex: 1;
    background: var(--brand-orange);
    color: var(--white);
    padding: 94px 0 0 45px;
  }
  .contact-name {
    font-size: 22px;
    font-weight: 600;
    letter-spacing: 0.3px;
    margin-bottom: 18px;
  }
  .contact-list { list-style: none; }
  .contact-list li {
    display: flex;
    align-items: center;
    gap: 7px;
    font-size: 16px;
    line-height: 24px;
  }
  .contact-list svg { width: 15px; height: 15px; fill: var(--white); flex: none; }

  .card-back {
    position: absolute;
    left: 292px; top: 505px;
    width: 615px; height: 352px;
    background: var(--black);
    box-shadow: 0 2px 4px rgba(0,0,0,0.35);
    text-align: center;
  }
  .back-brand {
    position: absolute;
    left: 0; right: 0; top: 130px;
    font-size: 56px;
    font-weight: 700;
    color: var(--brand-orange);
    letter-spacing: -0.5px;
  }
  .back-slogan {
    position: absolute;
    left: 0; right: 0; top: 280px;
    font-size: 21px;
    font-weight: 600;
    color: var(--white);
  }
</style>
</head>
<body>
<main class="canvas">
  <section class="card-front">
    <div class="front-brand">
      <span class="brand-dot"></span>
      <span class="brand-name">Hartuvo</span>
    </div>
    <div class="front-divider"></div>
    <div class="front-contact">
      <h1 class="contact-name">TOBIAS LINDQVIST</h1>
      <ul class="contact-list">
        <li>
          <svg viewBox="0 0 24 24" aria-hidden="true"><path d="M6.6 10.8a15.1 15.1 0 0 0 6.6 6.6l2.2-2.2a1 1 0 0 1 1-.25 11.4 11.4 0 0 0 3.6.57 1 1 0 0 1 1 1V20a1 1 0 0 1-1 1A17 17 0 0 1 3 4a1 1 0 0 1 1-1h3.5a1 1 0 0 1 1 1c0 1.25.2 2.45.57 3.57a1 1 0 0 1-.25 1z"/></svg>
          0031687203316
        </li>
        <li>
          <svg viewBox="0 0 24 24" aria-hidden="true"><path d="M2 5h20v14H2z" fill="none"/><path d="M2 5h20L12 12.5zM2 7.2l10 7.3 10-7.3V19H2z"/></svg>
          Tobias@hartuvo.nl
        </li>
        <li>
          <svg viewBox="0 0 24 24" aria-hidden="true"><path d="M12 2a10 10 0 1 0 0 20 10 10 0 0 0 0-20zm-1 17.9A8 8 0 0 1 4.1 10.4L9 15.3v1a2 2 0 0 0 2 2zm6.9-2.5A2 2 0 0 0 16 16h-1v-3a1 1 0 0 0-1-1H8v-2h2a1 1 0 0 0 1-1V7h2a2 2 0 0 0 2-2v-.4a8 8 0 0 1 2.9 12.8z"/></svg>
          www.hartuvo.nl
        </li>
      </ul>
    </div>
  </section>

  <section class="card-back">
    <div class="back-brand">Hartuvo</div>
    <p class="back-slogan">Because Quality Matters</p>
  </section>
</main>
</body>
</html>
```